Valdane Companies Business Card Design

We need a new business card for our Private Equity Real Estate Development firm, “Valdane” and our EB-5 regional center “Thornmere Regional Center” on one card. We prefer a design that is simple, elegant, and represents the luxury products we design and build as well as the financial security and stability our successful history has produced. We are an industry leader in our field and 3rd generation family business that has evolved into an institutional quality investment platform. Considered design size is standard business card dimensions (3.5 x 2 inches with an additional 1/8 inch space for design elements or backgrounds that extend beyond the finished size of your piece.

Target Market(s)

• High net worth individuals
• Highly skilled technical workers and physicians in the US seeking investment-based immigration opportunities
• Sophisticated private equity investors
• Intermediary partners include domestic attorneys and investment brokers, as well as international agent networks
• US real estate developers

Industry/Entity Type

Finance

Contact Information for Business Card

(Providing placeholder info for personal information, please design for longer character spaces, longer names and addresses etc..)
• Logo for Valdane
• Logo for Thornmere Regional Center
• Full name: Marcus Valdane
• Job title: CEO
• Email address: mvaldane@valdanecompanies.com
• Cell phone number: +1.555.314.2287
• Office number +1.555.628.4410
• Office address: Larkfield Court 5, 4817 Vista Orilla, Corvel Ridge, NV.
• Website: www.valdanecompanies.com

Font styles to use
Serif
Sans Serif

Colors
ec1f27
ffffff
000000

Requirements
Must have
• • Logo for Valdane
• • Logo for Thornmere Regional Center
• - Use rounded corners
• (See .ai file included for logos)
Nice to have
• • Simple, elegant design
• • Aesthetically compatible with our website design (www.valdanecompanies.com)
• • Color palette including but not limited to white, black, and red (as per logos)
Should not have
• - Not too much red color
• - Do not stack both logos on top of each other

```html
<!DOCTYPE html>
<html lang="en">
<head>
<meta charset="utf-8">
<title>Valdane Companies Business Card</title>
<link href="https://fonts.googleapis.com/css2?family=Cinzel:wght@400;700&family=Open+Sans:wght@400;600&display=swap" rel="stylesheet">
<style>
  :root {
    --stage: #2b2b2b;
    --card: #111111;
    --card-edge: #1c1c1c;
    --red: #ec1f27;
    --red-deep: #c4121a;
    --white: #ffffff;
    --soft-white: #e9e9e9;
    --steel: #8d8d8d;
    --steel-dim: #5f5f5f;
  }
  * { box-sizing: border-box; margin: 0; padding: 0; }
  html, body { width: 1200px; height: 716px; overflow: hidden; background: var(--stage); }
  .canvas {
    width: 1200px; height: 716px;
    display: flex; align-items: center; justify-content: center; gap: 48px;
  }
  .card {
    position: relative;
    width: 525px; height: 300px;
    background: var(--card);
    border: 1px solid var(--card-edge);
    border-radius: 20px;
    overflow: hidden;
  }

  /* Front */
  .front-brand {
    position: absolute; left: 70px; top: 96px;
    display: flex; align-items: center; gap: 18px;
  }
  .brand-square { width: 38px; height: 38px; background: var(--steel); }
  .brand-name {
    font-family: "Cinzel", serif; font-weight: 700;
    font-size: 40px; letter-spacing: 1px; color: var(--steel); line-height: 1;
  }
  .front-web {
    position: absolute; left: 72px; top: 196px;
    font-family: "Open Sans", sans-serif; font-size: 14px;
    letter-spacing: 2.5px; color: var(--steel-dim);
  }

  /* Back */
  .person { position: absolute; left: 40px; top: 34px; }
  .person-name {
    font-family: "Cinzel", serif; font-weight: 400;
    font-size: 24px; color: var(--white); letter-spacing: 1px; line-height: 1;
  }
  .person-title {
    font-family: "Open Sans", sans-serif; font-weight: 600;
    font-size: 9px; color: var(--red); letter-spacing: 1px; margin-top: 4px;
  }
  .rule { width: 36px; height: 3px; background: var(--red-deep); margin: 12px 0; }
  .contact-list { list-style: none; }
  .contact-list li {
    display: flex; align-items: center; gap: 9px;
    font-family: "Open Sans", sans-serif; font-size: 13px;
    color: var(--soft-white); line-height: 1.6;
  }
  .contact-list svg { width: 12px; height: 12px; fill: var(--red); flex: none; }
  .address li { align-items: flex-start; }
  .address svg { margin-top: 4px; }

  .center-brand {
    position: absolute; right: 34px; bottom: 36px;
    display: flex; align-items: center; gap: 12px;
  }
  .center-square { width: 26px; height: 26px; background: var(--red); }
  .center-name {
    font-family: "Cinzel", serif; font-weight: 700;
    font-size: 17px; color: var(--red); letter-spacing: 0.5px; line-height: 1.15;
    text-align: left;
  }
</style>
</head>
<body>
<main class="canvas">

  <section class="card card-front">
    <div class="front-brand">
      <span class="brand-square"></span>
      <span class="brand-name">Valdane Capital</span>
    </div>
    <p class="front-web">www.valdanecompanies.com</p>
  </section>

  <section class="card card-back">
    <div class="person">
      <h1 class="person-name">Marcus Valdane</h1>
      <p class="person-title">CEO</p>
      <div class="rule"></div>
      <ul class="contact-list">
        <li>
          <svg viewBox="0 0 12 12" aria-hidden="true"><path d="M0 2h12v8H0z M0 2l6 4.5L12 2" fill="none" stroke="#ec1f27" stroke-width="1.4"/></svg>
          mvaldane@valdanecompanies.com
        </li>
        <li>
          <svg viewBox="0 0 12 12" aria-hidden="true"><rect x="3" y="0" width="6" height="12" rx="1"/><rect x="4" y="1.5" width="4" height="7" fill="#111"/></svg>
          +1.555.314.2287
        </li>
        <li>
          <svg viewBox="0 0 12 12" aria-hidden="true"><path d="M2.5 0.5l2 2.5-1.2 1.4a7 7 0 0 0 4.3 4.3L9 7.5l2.5 2-1.2 2A10 10 0 0 1 0.5 1.7z"/></svg>
          +1.555.628.4410
        </li>
      </ul>
      <div class="rule"></div>
      <ul class="contact-list address">
        <li>
          <svg viewBox="0 0 12 12" aria-hidden="true"><path d="M6 0a4 4 0 0 1 4 4c0 3-4 8-4 8S2 7 2 4a4 4 0 0 1 4-4z"/><circle cx="6" cy="4" r="1.5" fill="#111"/></svg>
          <span>Larkfield Court 5, 4817 Vista Orilla<br>Corvel Ridge, NV.</span>
        </li>
      </ul>
    </div>
    <div class="center-brand">
      <span class="center-square"></span>
      <span class="center-name">Thornmere<br>Regional Center</span>
    </div>
  </section>

</main>
</body>
</html>
```